Veltrano.co - Polar Expeditions Specialists

We need a modern, visually striking business card for Veltrano.co, a company specialized in selling expedition cruises to the most remote regions on Earth, with a focus on the Arctic and Antarctica. The design should instantly communicate that the cardholder is an expert in polar travel. Use clean, premium aesthetics with cool tones like icy blue and white, possibly incorporating polar imagery (ice, glaciers, penguins, etc.)

Attached the logo

Contact Information for Business Card

Feels high-end and trustworthy.. Visually memorable — encourages people to keep it

Colors
0054AA
0677BA
7BADD7
CADEEF
E8F1F8

Requirements
Must have
• ice, glaciers, penguins, montains
Nice to have
• modern, transparente,

```html
<!DOCTYPE html>
<html lang="en">
<head>
<meta charset="utf-8">
<title>Veltrano.co – Business Card</title>
<link rel="stylesheet" href="https://fonts.googleapis.com/css2?family=Montserrat:wght@400;700&family=Poppins:wght@600;700&display=swap">
<style>
  :root {
    --blue-deep: #0054AA;
    --blue-brand: #2B78BA;
    --blue-photo: #5A93CC;
    --blue-mid: #7BADD7;
    --blue-ice: #CADEEF;
    --blue-mist: #E8F1F8;
    --white: #FFFFFF;
    --ink: #3A3A3A;
    --backdrop: #E6E7E9;
  }
  * { box-sizing: border-box; margin: 0; padding: 0; }
  html, body { width: 1200px; height: 900px; overflow: hidden; }
  body {
    background: var(--backdrop);
    display: flex;
    flex-direction: column;
    align-items: center;
    justify-content: center;
    gap: 40px;
    font-family: "Montserrat", sans-serif;
  }
  .card {
    width: 660px;
    height: 377px;
    border-radius: 26px;
    overflow: hidden;
    position: relative;
    box-shadow: 0 10px 24px rgba(0,0,0,0.18);
  }

  /* Front */
  .card-front { background: var(--blue-photo); }
  .front-photo {
    position: absolute; inset: 0;
    background: radial-gradient(ellipse 45% 55% at 55% 50%, #8DB6DF 0%, #6A9FD3 45%, var(--blue-photo) 100%);
  }
  .front-brand {
    position: absolute; inset: 0;
    display: flex; align-items: center; justify-content: center; gap: 16px;
    color: var(--white);
  }
  .brand-dot {
    width: 54px; height: 54px; border-radius: 50%;
    background: var(--white);
  }
  .brand-name {
    font-family: "Poppins", sans-serif;
    font-weight: 700;
    font-size: 60px;
    line-height: 1;
    letter-spacing: 0.5px;
  }
  .brand-tagline {
    font-family: "Poppins", sans-serif;
    font-weight: 600;
    font-size: 15px;
    letter-spacing: 0.6px;
    margin-top: 6px;
  }

  /* Back */
  .card-back { background: var(--white); display: flex; }
  .back-band {
    width: 188px;
    background: var(--blue-brand);
    position: relative;
  }
  .band-brand {
    position: absolute;
    left: 50%; top: 50%;
    transform: translate(-50%, -50%) rotate(-90deg);
    display: flex; align-items: center; gap: 12px;
    color: var(--white);
    white-space: nowrap;
  }
  .band-brand .brand-dot { width: 38px; height: 38px; }
  .band-brand .brand-name { font-size: 44px; }
  .band-brand .brand-tagline { font-size: 12px; margin-top: 4px; }

  .back-details {
    flex: 1;
    padding: 64px 0 0 60px;
    color: var(--ink);
  }
  .holder-name {
    font-weight: 700;
    font-size: 34px;
    color: var(--blue-brand);
    letter-spacing: 1px;
    line-height: 1;
  }
  .holder-role { font-size: 20px; margin-top: 6px; }
  .address { font-size: 17px; line-height: 1.35; margin-top: 22px; }
  .contact-list { list-style: none; margin-top: 18px; }
  .contact-list li {
    display: flex; align-items: center; gap: 12px;
    font-size: 17px; line-height: 1.5;
  }
  .contact-icon { width: 15px; height: 15px; fill: var(--blue-brand); flex: none; }
</style>
</head>
<body>

  <section class="card card-front" aria-label="Card front">
    <div class="front-photo" role="img" aria-label="Photo of a polar bear on snow and ice, tinted blue"></div>
    <div class="front-brand">
      <span class="brand-dot"></span>
      <div>
        <div class="brand-name">Veltrano.co</div>
        <div class="brand-tagline">Polar Expeditions Specialists</div>
      </div>
    </div>
  </section>

  <section class="card card-back" aria-label="Card back">
    <div class="back-band">
      <div class="band-brand">
        <span class="brand-dot"></span>
        <div>
          <div class="brand-name">Veltrano.co</div>
          <div class="brand-tagline">Polar Expeditions Specialists</div>
        </div>
      </div>
    </div>
    <div class="back-details">
      <h1 class="holder-name">HENRIK DALBY</h1>
      <p class="holder-role">CEO / Founder</p>
      <p class="address">P.O. Box 8574 Streen Name<br>Country Name AV 5234</p>
      <ul class="contact-list">
        <li>
          <svg class="contact-icon" viewBox="0 0 16 16" aria-hidden="true"><path d="M3 1h3l1.5 4-2 1.3a9 9 0 0 0 4.2 4.2L11 8.5l4 1.5v3a2 2 0 0 1-2 2A12 12 0 0 1 1 3a2 2 0 0 1 2-2z"/></svg>
          +43 600 48 21 937
        </li>
        <li>
          <svg class="contact-icon" viewBox="0 0 16 16" aria-hidden="true"><path d="M1 3h14v10H1z M1 3l7 5 7-5" fill="none" stroke="#2B78BA" stroke-width="1.8" stroke-linejoin="round"/></svg>
          henrik.dalby@veltrano.co
        </li>
        <li>
          <svg class="contact-icon" viewBox="0 0 16 16" aria-hidden="true"><circle cx="8" cy="8" r="6.5" fill="none" stroke="#2B78BA" stroke-width="1.6"/><path d="M1.5 8h13M8 1.5c-3 3.5-3 9.5 0 13M8 1.5c3 3.5 3 9.5 0 13" fill="none" stroke="#2B78BA" stroke-width="1.3"/></svg>
          www.veltrano.co
        </li>
      </ul>
    </div>
  </section>

</body>
</html>
```